Brindle Healthcare Coming Soon Sign

I need a large (10 x5) road banner announcing the construction of our new medical practice at 5187 Larkmoor Road in John's Island. The name of our practice is Brindle Healthcare and we thought it would be fund to nick name it the "Brindle Waystation". We'd like the tagline to read - "There's nothing healthy about driving an hour to see your doctor. So we're coming to you." Opening Late 2025 I have attached three logos as we have two other practices (Brindle Urgent and Brindle Aesthetics ) that should be present on the bottom of the sign but the main business is Brindle Healthcare. For more information on our look/feel visit our website www.goplainway-example.com (which should be somewhere on the banner as well)
Updates

The signage needs to say Coming Late Fall 2025!

Target Market(s)

Drive By traffic must be made aware that we are coming soon

Industry/Entity Type

Healthcare

Requirements
Nice to have
• Western Theme

```html
<!DOCTYPE html>
<html lang="en">
<head>
<meta charset="utf-8">
<title>Brindle Healthcare – Coming Late Fall 2025</title>
<link rel="stylesheet" href="https://fonts.googleapis.com/css2?family=Montserrat:wght@600&family=Roboto+Condensed:wght@500;600&family=Roboto:wght@500&display=swap">
<style>
  :root{
    --page:#e9edf2;
    --frame-line:#1f2b52;
    --frame-white:#ffffff;
    --navy:#3d4a7c;
    --navy-deep:#2e3a68;
    --sky:#6db0e3;
    --sky-light:#8cc4ee;
    --ink:#1e2b57;
    --white:#ffffff;
    --tag-red:#e8403a;
    --tag-dark:#c92a25;
  }
  *{box-sizing:border-box;margin:0;padding:0}
  html,body{width:1200px;height:798px;overflow:hidden;background:var(--page)}
  .banner{
    position:absolute;left:20px;top:109px;width:1160px;height:580px;
    background:var(--frame-white);border:2px solid var(--frame-line);
  }
  .banner-art{position:absolute;inset:0}
  .brand{
    position:absolute;left:44px;top:62px;display:flex;align-items:center;gap:16px;
  }
  .brand-mark{width:58px;height:58px;border:4px solid var(--white);border-radius:8px}
  .brand-name{
    font-family:"Montserrat",sans-serif;font-weight:600;color:var(--white);
    font-size:26px;letter-spacing:5px;line-height:1.25;text-transform:uppercase;
  }
  .opening-tag{
    position:absolute;left:755px;top:68px;height:56px;padding:0 40px 0 16px;
    background:var(--tag-red);border-radius:12px 0 0 12px;
    font-family:"Roboto",sans-serif;font-weight:500;font-size:30px;color:var(--white);
    display:flex;align-items:center;
  }
  .opening-tag::after{
    content:"";position:absolute;right:0;top:0;width:14px;height:100%;
    background:repeating-linear-gradient(var(--tag-dark) 0 10px,transparent 10px 14px);
  }
  .tagline{
    position:absolute;left:0;right:0;top:192px;text-align:center;
    font-family:"Roboto Condensed",sans-serif;font-weight:600;font-size:43px;
    line-height:60px;color:var(--white);
  }
  .sister-practices{
    position:absolute;left:0;right:0;top:402px;display:flex;justify-content:center;gap:44px;
  }
  .sister{
    font-family:"Montserrat",sans-serif;font-weight:600;color:var(--white);
    font-size:22px;letter-spacing:4px;line-height:1.15;text-transform:uppercase;
  }
  .footer-line{
    position:absolute;top:534px;font-family:"Roboto",sans-serif;font-weight:500;
    font-size:27px;color:var(--ink);
  }
  .address{left:90px}
  .website{right:28px;display:flex;align-items:center;gap:10px;letter-spacing:0.5px}
  .globe{width:36px;height:36px}
</style>
</head>
<body>
  <section class="banner">
    <svg class="banner-art" viewBox="0 0 1156 576" width="1156" height="576" aria-hidden="false">
      <defs>
        <linearGradient id="photoTone" x1="0" y1="0" x2="1" y2="1">
          <stop offset="0" stop-color="#3a4676"/>
          <stop offset="0.55" stop-color="#435284"/>
          <stop offset="1" stop-color="#384672"/>
        </linearGradient>
      </defs>
      <rect role="img" aria-label="Photo of the new practice building, tinted navy" x="9" y="9" width="1138" height="558" fill="url(#photoTone)"/>
      <path d="M9 392 Q578 612 1147 392 L1147 567 L9 567 Z" fill="var(--sky-light)"/>
      <path d="M9 400 Q578 620 1147 400 L1147 567 L9 567 Z" fill="var(--navy-deep)"/>
      <path d="M9 416 Q578 636 1147 416 L1147 567 L9 567 Z" fill="var(--sky)"/>
    </svg>

    <div class="brand">
      <span class="brand-mark"></span>
      <div class="brand-name">Brindle<br>Healthcare</div>
    </div>

    <div class="opening-tag">Coming Late Fall 2025!</div>

    <p class="tagline">There's Nothing Healthy About Driving An<br>Hour To See Your Doctor. So We're Coming To You.</p>

    <div class="sister-practices">
      <div class="sister">Brindle<br>Aesthetics</div>
      <div class="sister">Brindle<br>Urgent</div>
    </div>

    <p class="footer-line address">5187 Larkmoor Road in John's Island</p>
    <p class="footer-line website">
      <svg class="globe" viewBox="0 0 36 36" fill="none" stroke="var(--ink)" stroke-width="2">
        <circle cx="18" cy="18" r="15"/>
        <ellipse cx="18" cy="18" rx="6.5" ry="15"/>
        <line x1="3" y1="18" x2="33" y2="18"/>
        <path d="M6 10 H30 M6 26 H30"/>
      </svg>
      www.goplainway-example.com
    </p>
  </section>
</body>
</html>
```